Velmisa Sunscreen and Tanning Lotion Flyer

I need a flyer to post to pm Chatterloop and other social media.
It most have these components:
Modern, sensational fonts, Original Art work, Sexy, Theme based on Verses
Women, bikini, tan, attractive
Ocean scenes, Palm Trees (same green as bottle)
VELMISA Logo (Slight shading background)
Quote “Quality by Design”
Bright, Sunny, fun
Save in PDF, GIF, and EPS

Reason: I have some designer who have not completed their work. Thank you.

Target Market(s)

Sunscreen tanning lotion

Industry/Entity Type

Media

Colors
9bcb3c

Requirements
Must have
• Modern, sensational fonts, Original Art work, Sexy, Theme based on Verses
• Women, bikini, tan, attractive
• Ocean scenes, Palm Trees (same green as bottle)
• VELMISA Logo (Slight shading in the background)
• Quote “Quality by Design”
• Bright, Sunny, fun
• Save in PDF, GIF, and EPS
Nice to have
• flyer designed with these verses in mind.
• •When the warm sea breeze exhales its sweet serenity, and the frothy sea cloaks your body in indulgence, the rays of the sun completes the objective.
• • The water splatters against the shore, and the blue stillness showers me tranquility and perfection and I find myself covered by the seas delightful symphony.
• •The sea breeze feels like a long lost friend, as it delightfully caresses your sweaty skin. And like that long lost friend, you embrace, take a deep breath, and relish the gusto of life.
• • The stunningly-turquoise sea beckons and we enthusiastically surrender to its allure. A smile from the white puffy clouds above. A soothing massage from the wet, cool sand below our feet, bliss in the sun.
• •Seagulls have white plumage, not unlike the color to the clouds overhead. Their hue is undistinguishable from the whitecaps spawned by waves on a blustery day. Mother Nature must be an artist whose philosophy is harmony in symmetry
• It would be nice to have these verses incorporated in the Flyer, but it is not necessary.
Should not have
• Must not have someone else's work, all graphic need to be original.

```html
<!DOCTYPE html>
<html lang="en">
<head>
<meta charset="utf-8">
<title>Velmisa Suntan Lotion Flyer</title>
<link rel="stylesheet" href="https://fonts.googleapis.com/css2?family=Marcellus&family=Open+Sans:wght@400;600;700;800&family=Alegreya:ital@0;1&family=Almendra:wght@700&family=Cormorant+Garamond:wght@500&family=Audiowide&family=Lora:ital@1&display=swap">
<style>
  :root {
    --ink-dark: #040706;
    --teal-deep: #0b4647;
    --teal-mid: #136b70;
    --gold: #c9a06a;
    --copy-yellow: #e9e27c;
    --orange: #f2a42a;
    --email-yellow: #f4dc4a;
    --lime: #9bcb3c;
    --lime-light: #d9f25e;
    --lime-dark: #2f9a36;
    --ocean-blue: #1b8fce;
    --arc-blue: #2aa6d6;
    --arc-orange: #d9874a;
    --white: #ffffff;
    --spf-ink: #10210c;
  }
  * { margin: 0; padding: 0; box-sizing: border-box; }
  html, body { width: 1200px; height: 822px; overflow: hidden; background: #2b1b0e; }
  .flyer {
    position: relative;
    width: 1200px; height: 822px; overflow: hidden;
    background: linear-gradient(90deg, var(--ink-dark) 0%, #061413 22%, var(--teal-deep) 42%, var(--teal-mid) 60%, var(--teal-deep) 100%);
    font-family: "Open Sans", sans-serif;
    color: var(--white);
  }
  .scene { position: absolute; inset: 0; width: 1200px; height: 822px; }
  .brand { position: absolute; left: 37px; top: 196px; }
  .brand-name {
    font-family: "Marcellus", serif; font-size: 66px; line-height: 1;
    color: var(--gold); letter-spacing: 1px;
  }
  .brand-name sup { font-size: 22px; vertical-align: 32px; }
  .brand-sub {
    font-family: "Open Sans", sans-serif; font-size: 28px; color: var(--gold);
    margin: 4px 0 0 42px; letter-spacing: 0.5px;
  }
  .story {
    position: absolute; left: 30px; top: 334px; width: 298px;
    font-family: "Alegreya", serif; font-size: 12.6px; line-height: 18.6px;
    color: var(--copy-yellow); text-align: justify; letter-spacing: -0.2px;
  }
  .origin {
    position: absolute; left: 30px; top: 688px; width: 374px;
    font-weight: 600; font-size: 19.5px; color: var(--orange);
    padding-bottom: 3px; border-bottom: 1px solid var(--orange);
  }
  .contact-note {
    position: absolute; left: 30px; top: 727px;
    font-family: "Lora", serif; font-style: italic; font-size: 16px;
  }
  .contact-email {
    position: absolute; left: 30px; top: 758px;
    font-weight: 700; font-size: 29px; letter-spacing: 1.5px; color: var(--email-yellow);
  }
  .badge {
    position: absolute; border-radius: 50%;
    background: radial-gradient(circle at 45% 30%, var(--lime-light) 0%, var(--lime) 45%, var(--lime-dark) 100%);
    box-shadow: 0 0 0 3px rgba(255,255,255,0.35), 0 4px 10px rgba(0,0,0,0.4);
    display: flex; flex-direction: column; align-items: center; justify-content: center; text-align: center;
  }
  .badge-uv { left: 471px; top: 111px; width: 200px; height: 206px; }
  .badge-uv p {
    font-family: "Almendra", serif; font-weight: 700; font-size: 29px; line-height: 36px;
    text-shadow: 0 2px 3px rgba(0,0,0,0.45);
  }
  .badge-spf { left: 962px; top: 511px; width: 200px; height: 206px; justify-content: flex-start; padding-top: 42px; }
  .spf-value { font-weight: 800; font-size: 58px; line-height: 1; -webkit-text-stroke: 2px #1a2a12; }
  .spf-value span { font-size: 30px; }
  .spf-volume { font-weight: 700; font-size: 19px; color: var(--spf-ink); margin-top: 12px; }
  .headline-new {
    position: absolute; left: 420px; top: 362px;
    font-family: "Cormorant Garamond", serif; font-weight: 500; font-size: 132px; line-height: 1;
    text-shadow: 0 3px 6px rgba(0,0,0,0.35);
  }
  .headline-tag {
    position: absolute; left: 420px; font-family: "Audiowide", sans-serif;
    text-shadow: 0 2px 5px rgba(0,0,0,0.4);
  }
  .tag-one { top: 520px; font-size: 45px; letter-spacing: 1px; }
  .tag-two { top: 580px; font-size: 36px; letter-spacing: 2px; word-spacing: 14px; }
  .signoff { position: absolute; right: 33px; top: 714px; text-align: right; font-weight: 600; }
  .signoff-brand { font-size: 19px; line-height: 24px; }
  .signoff-product { font-size: 20px; line-height: 26px; }
  .signoff-motto, .signoff-person { font-size: 13.5px; line-height: 19px; }
</style>
</head>
<body>
<main class="flyer">
  <svg class="scene" viewBox="0 0 1200 822" aria-hidden="false">
    <defs>
      <linearGradient id="beach" x1="0" y1="0" x2="0" y2="1">
        <stop offset="0" stop-color="#2c8fcf"/>
        <stop offset="0.4" stop-color="#7fc3e6"/>
        <stop offset="0.55" stop-color="#1f7ea0"/>
        <stop offset="1" stop-color="#0a5a72"/>
      </linearGradient>
      <linearGradient id="tanTone" x1="0" y1="0" x2="1" y2="0">
        <stop offset="0" stop-color="#0b5d78" stop-opacity="0"/>
        <stop offset="0.7" stop-color="#0b5d78" stop-opacity="0"/>
        <stop offset="1" stop-color="#6aa33a" stop-opacity="0.35"/>
      </linearGradient>
      <clipPath id="photoClip"><circle cx="840" cy="448" r="470"/></clipPath>
    </defs>
    <g role="img" aria-label="Beach photograph: tanned woman in a white bikini by the turquoise ocean, palm fronds overhead">
      <rect x="360" y="0" width="840" height="822" fill="url(#beach)" clip-path="url(#photoClip)"/>
      <rect x="360" y="0" width="840" height="822" fill="url(#tanTone)" clip-path="url(#photoClip)"/>
    </g>
    <g fill="none" stroke-width="2">
      <circle cx="840" cy="448" r="478" stroke="var(--arc-blue)"/>
      <circle cx="848" cy="452" r="490" stroke="var(--arc-blue)" stroke-opacity="0.6"/>
      <path d="M380 640 Q520 820 820 822" stroke="var(--arc-orange)"/>
      <path d="M395 660 Q560 830 860 822" stroke="var(--arc-orange)" stroke-opacity="0.7"/>
    </g>
    <path d="M900 700 Q1050 650 1200 640 L1200 822 L900 822 Q890 760 900 700 Z" fill="var(--ocean-blue)"/>
    <path d="M900 700 Q1050 650 1200 640" fill="none" stroke="var(--lime)" stroke-width="3"/>
  </svg>

  <div class="brand">
    <div class="brand-name">VELMISA<sup>™</sup></div>
    <div class="brand-sub">SUNTAN LOTION</div>
  </div>

  <p class="story">Velmisa Tanning Lotion is the most extra ordinary and innovative sun tanning product to emerge in several generations. The constituents of this product are formidable substances that protect the skin against the aftermath of sun exposure before you expose yourself to the sun's rays. The Aloe Vera in this product along with other oils and cream are specifically manufactured to lessen the symptoms of extended exposure to the sun. Velmisa is designed to provide a broad spectrum protection (50) that assists in the way it helps your skin to create a magnificent sun absorbing and long lasting deep dark bronzing experience. It is an elegant gift from nature that leaves your skin feeling fresh and not greasy. It is water resistant, contains no preservatives or coloring agents. Velmisa Tanning Lotion is manufactured utilizing the finest raw materials obtainable that are grown and imported from various regions of the world.</p>

  <p class="origin">Product of the USA: Harbor Point, NJ</p>
  <p class="contact-note">For comments or suggestions please contact us at</p>
  <p class="contact-email">velmisa87@gmail.com</p>

  <div class="badge badge-uv"><p>Reduction<br>to (UVA)<br>and (UVB)<br>radiation</p></div>

  <h1 class="headline-new">New</h1>
  <p class="headline-tag tag-one">SOPHISTICATED</p>
  <p class="headline-tag tag-two">VELVETY SMOOTH</p>

  <div class="badge badge-spf">
    <div class="spf-value">50<span>SPF</span></div>
    <div class="spf-volume">8FL OZI 237ml</div>
  </div>

  <div class="signoff">
    <p class="signoff-brand">VELMISA™</p>
    <p class="signoff-product">Tanning Lotion &amp; Sunscreen</p>
    <p class="signoff-motto">Quality by Design</p>
    <p class="signoff-person">Dario Montes-COO</p>
  </div>
</main>
</body>
</html>
```